Roofing Contractor business card redesign

I want to redesign my business card with a fresh, eye catching concept

Target Market(s)

Residential Roofing Clients, potential employees, and subcontractors.

Industry/Entity Type

Business

Colors

Designer to choose colors to be used in the design.

Requirements
Nice to have
• I just want something that's more pleasing to the eye. You can use a combination of either / or of my logos.

```html
<!DOCTYPE html>
<html lang="en">
<head>
<meta charset="utf-8">
<title>Steady Crew – Business Card</title>
<link href="https://fonts.googleapis.com/css2?family=Fjalla+One&family=Ropa+Sans&display=swap" rel="stylesheet">
<style>
  :root {
    --backdrop: #3a3a3a;
    --card-white: #f4f4f4;
    --brand-orange: #f0912c;
    --orange-deep: #e8671f;
    --orange-light: #f5b23c;
    --brown: #3e1f14;
    --text-dark: #3b2a25;
  }
  * { margin: 0; padding: 0; box-sizing: border-box; }
  html, body { width: 1200px; height: 960px; overflow: hidden; }
  body { background: var(--backdrop); position: relative; font-family: "Ropa Sans", sans-serif; }

  .card { position: absolute; width: 600px; height: 343px; overflow: hidden; }

  .card-front { left: 320px; top: 103px; background: var(--card-white); }
  .accent-bar {
    position: absolute; left: 0; top: 60px; width: 8px; height: 63px;
    background: linear-gradient(180deg, var(--brand-orange), var(--orange-light));
  }
  .contact { position: absolute; left: 35px; top: 58px; color: var(--text-dark); }
  .contact-name {
    font-family: "Fjalla One", sans-serif; font-weight: 400;
    font-size: 27px; line-height: 30px; color: var(--brand-orange); letter-spacing: 0.3px;
  }
  .contact-title, .contact-address, .contact-lines { font-size: 14.5px; line-height: 18px; }
  .contact-address { margin-top: 12px; margin-left: 1px; }
  .contact-lines { margin-top: 15px; margin-left: 3px; }
  .crew-illustration {
    position: absolute; left: 265px; top: 12px; width: 320px; height: 320px; border-radius: 50%;
    background: radial-gradient(circle at 50% 45%, var(--orange-light) 0%, var(--orange-deep) 38%, var(--brown) 62%);
    border: 4px solid #fff; box-shadow: 0 0 0 1px #ddd;
  }

  .card-back {
    left: 317px; top: 488px;
    background: linear-gradient(135deg, var(--orange-light) 0%, var(--brand-orange) 30%, var(--orange-deep) 75%);
  }
  .brand { position: absolute; left: 0; right: 0; top: 104px; text-align: center; color: var(--brown); font-family: "Fjalla One", sans-serif; }
  .brand-name { display: flex; align-items: center; justify-content: center; gap: 14px; font-size: 60px; line-height: 70px; }
  .brand-mark { width: 64px; height: 64px; border-radius: 50%; background: var(--brown); }
  .brand-tagline { font-size: 29px; line-height: 34px; margin-top: 6px; }

  .social-row { position: absolute; left: 140px; top: 282px; }
</style>
</head>
<body>
  <section class="card card-front">
    <div class="accent-bar"></div>
    <div class="contact">
      <h1 class="contact-name">DALE MORROW</h1>
      <p class="contact-title">Kestrel Certified Roof Inspector<br>Licensed Property Adjuster</p>
      <p class="contact-address">4820 Alder Ridge Road<br>Suite 118<br>Dallas, TX 75000</p>
      <p class="contact-lines">Office: (555) 210-4300<br>Mobile/Text: (555) 287-6614<br>dale@steadycrewtx.com<br>www.steadycrewtx.com</p>
    </div>
    <div class="crew-illustration" role="img" aria-label="Illustration of a roofing crew with tools in front of a house roof"></div>
  </section>

  <section class="card card-back">
    <div class="brand">
      <div class="brand-name"><span>Steady</span><span class="brand-mark"></span><span>Crew</span></div>
      <div class="brand-tagline">General Contractors, Inc.</div>
    </div>
    <svg class="social-row" width="320" height="30" viewBox="0 0 320 30" aria-label="Social media links">
      <g stroke="var(--brown)" stroke-width="1.5" fill="none">
        <line x1="0" y1="15" x2="78" y2="15"/>
        <line x1="242" y1="15" x2="320" y2="15"/>
        <circle cx="95" cy="15" r="13"/>
        <circle cx="127.5" cy="15" r="13"/>
        <circle cx="160" cy="15" r="13"/>
        <circle cx="192.5" cy="15" r="13"/>
        <circle cx="225" cy="15" r="13"/>
      </g>
    </svg>
  </section>
</body>
</html>
```